Refresh of far from plain IT company website

Our web site is starting to show it's age. You can see the existing site here: www.plumbwick.net. As a growing company we want to come across as a dynamic collection of IT experts.

We want to update the design so are open to any colour palette and look, but want to retain our current table logo. We use the logo on our business cards but with a white background - see the attached file, so you don't need to keep the brown or the green.

The design should consider the range of browsers that will be looking at the site - so please show how it will look on a wide screen laptop and a 768x1024 tablet.

We want to add some pages about our team and their skills, probably with photos of each person on the team.

This is an uncoded project - the PSD files of the design is required, not coding.
Updates

Thanks everyone for the submissions so far.  It's a holiday day in the UK today but we will get some feedback on the designs so far out to you.

Target Market(s)

Architects and other creative types looking for IT support

Industry/Entity Type

Business

Font styles to use
Serif
Sans Serif

Requirements
Must have
• Must look good on a laptop and an iPad.

```html
<!DOCTYPE html>
<html lang="en">
<head>
<meta charset="utf-8">
<title>plumbwick – IT support</title>
<link rel="stylesheet" href="https://fonts.googleapis.com/css2?family=Lato:wght@300;400;700&family=Oswald:wght@300;400&display=swap">
<style>
:root{
  --brand:#a3154f;
  --ink:#333;
  --muted:#777;
  --tile:#7c9b92;
  --tile-dark:#a8bdb7;
  --topbar:#3a3a3a;
  --footer:#303030;
  --footer-deep:#262626;
  --field:#1f1f1f;
  --line:#e3e3e3;
  --link-date:#3d8fd1;
}
*{box-sizing:border-box;margin:0;padding:0}
html,body{width:676px;height:1200px;overflow:hidden}
body{font-family:'Lato',sans-serif;color:var(--ink);background:#fff;position:relative}
.abs{position:absolute}
.topbar{top:0;left:0;width:676px;height:18px;background:var(--topbar);color:#ddd;font-size:8px;display:flex;justify-content:flex-end;align-items:center;gap:12px;padding-right:78px}
.topbar span{display:flex;align-items:center;gap:5px}
.header{top:18px;left:0;width:676px;height:48px;border-bottom:1px solid var(--line)}
.brand{left:80px;top:12px;display:flex;align-items:center;gap:8px}
.brand-mark{width:18px;height:18px;background:var(--brand)}
.brand-name{font-size:21px;font-weight:700;color:var(--brand)}
.nav{right:76px;top:17px;display:flex;gap:0;font-size:8.5px;color:#555}
.nav a{color:inherit;text-decoration:none;padding:4px 8px}
.nav a.active{background:var(--brand);color:#fff;border-radius:2px}
.hero{top:66px;left:0;width:676px;height:222px;background:linear-gradient(160deg,#c9d0d0 0%,#e6e9e8 45%,#b9c2c3 100%)}
.hero-devices{left:74px;top:24px;width:272px;height:172px;border-radius:4px;background:linear-gradient(135deg,#1c1c1c 0%,#2e86b6 55%,#d7d7d7 100%)}
.hero-title{left:368px;top:58px;font-family:'Oswald',sans-serif;font-weight:400;font-size:24.5px;line-height:32px;color:#2f3d44}
.hero-arrows{left:558px;top:257px;display:flex;gap:5px}
.hero-arrows svg{width:18px;height:18px}
.welcome-title{left:74px;top:306px;width:170px;text-align:center;font-weight:300;font-size:25px;letter-spacing:.5px}
.welcome-sub{left:74px;top:334px;width:170px;text-align:center;font-weight:300;font-size:14px;color:#444}
.welcome-rule{left:239px;top:303px;width:1px;height:54px;background:#ddd}
.welcome-text{left:256px;top:309px;width:330px;font-size:8.5px;line-height:13.5px;color:#777;font-weight:300}
.divider{left:74px;top:372px;width:528px;height:1px;background:#eee}
.services{left:74px;top:389px;display:flex;gap:5.5px}
.service{width:101px;height:91px;background:var(--tile);position:relative}
.service .ico{position:absolute;left:28px;top:10px;width:45px;height:45px;border-radius:50%;background:#fff;display:flex;align-items:center;justify-content:center}
.service .label{position:absolute;left:0;bottom:0;width:100%;height:22px;border-top:1px solid var(--tile-dark);color:#fff;font-weight:300;font-size:13px;text-align:center;line-height:21px}
.mission{top:502px;left:0;width:676px;height:172px;background:linear-gradient(90deg,#fbfaf8 0%,#f2eee9 50%,#e8e3dc 80%,#f6f4f1 100%)}
.mission-photo{left:440px;top:6px;width:154px;height:166px;background:linear-gradient(180deg,#d9c2aa 0%,#3b4150 45%,#23283a 100%);border-radius:60px 60px 0 0}
.mission h2{position:absolute;left:75px;top:10px;font-weight:300;font-size:23px;color:#333}
.mission p.lead{position:absolute;left:75px;top:43px;width:370px;font-size:9px;line-height:13.5px;color:#333}
.mission h3{position:absolute;left:75px;top:75px;font-size:9px;font-weight:700}
.mission ul{position:absolute;left:80px;top:95px;width:340px;font-size:8.3px;line-height:12px;color:#444;list-style:none}
.mission li{position:relative;padding-left:11px;margin-bottom:8px}
.mission li::before{content:"";position:absolute;left:0;top:4.5px;width:3.5px;height:3.5px;border-radius:50%;background:#333}
.testi-title{top:686px;left:0;width:676px;text-align:center;font-weight:300;font-size:24px}
.testi{width:246px;height:78px;border:1px solid #ddd;border-radius:3px;background:#fff}
.testi::after{content:"";position:absolute;left:26px;bottom:-9px;width:12px;height:12px;background:#fff;border-right:1px solid #ddd;border-bottom:1px solid #ddd;transform:skewY(45deg) rotate(0);}
.testi .avatar{position:absolute;left:8px;top:11px;width:50px;height:50px;border-radius:50%;border:1px solid #ddd;background:radial-gradient(circle at 50% 40%,#c9b6a5,#eef0f1 70%)}
.testi p{position:absolute;left:66px;top:12px;width:172px;font-size:6.8px;line-height:11px;color:#555}
.testi p b{color:#ccc;font-size:11px;font-weight:700;margin-right:3px}
.client{font-size:7.5px;font-weight:700;color:#333}
.team{top:846px;left:0;width:676px;height:164px;background:linear-gradient(180deg,#b9c4c4 0%,#dde2e1 55%,#e9ecea 100%)}
.team h2{position:absolute;top:14px;width:100%;text-align:center;font-weight:300;font-size:24px;color:#333}
.team-row{position:absolute;left:107px;top:51px;display:flex;gap:9px}
.member{width:85px;text-align:center}
.member .photo{width:85px;height:78px;border:3px solid #fff;background:linear-gradient(160deg,#e8e2dc,#9a8576 60%,#3e4b63)}
.member span{display:block;margin-top:6px;font-size:7px;color:#555}
.team-arrow{top:82px;width:18px;height:18px}
.footer{top:1010px;left:0;width:676px;height:158px;background:var(--footer);color:#ccc}
.footer h4{position:absolute;top:16px;font-weight:400;font-size:10.5px;color:#eee}
.qlinks{position:absolute;left:74px;top:41px;display:grid;grid-template-columns:65px 60px;row-gap:11px;font-size:7.3px;color:#ddd;list-style:none}
.qlinks li::before{content:"";display:inline-block;width:4px;height:4px;margin-right:6px;vertical-align:1px;background:radial-gradient(circle,#aaa 35%,transparent 40%) 0 0/2px 2px}
.news{position:absolute;left:201px;width:130px;font-size:7px;line-height:10.5px;color:#ccc}
.news b{display:block;color:#eee;font-weight:700}
.news i{color:var(--link-date)}
.contact{position:absolute;left:346px;top:38px;font-size:7.3px;line-height:10.5px;color:#ddd}
.contact .row{display:flex;gap:9px;margin-bottom:6px}
.contact svg{width:10px;height:10px;flex:none;margin-top:1px}
.qc-field{position:absolute;left:488px;width:114px;height:19px;background:var(--field);font-size:6.5px;color:#aaa;padding:5px 6px}
.qc-submit{left:488px;top:127px;width:38px;height:14px;background:#ddd;color:#333;font-size:7px;font-weight:700;text-align:center;line-height:14px}
.bottombar{top:1168px;left:0;width:676px;height:32px;background:var(--footer-deep)}
.sub-field{left:74px;top:8px;width:131px;height:16px;border:1px solid #444;font-size:7px;color:#999;padding:3px 6px}
.sub-go{left:210px;top:8px;width:23px;height:16px;background:#ddd;color:#333;font-size:7px;font-weight:700;text-align:center;line-height:16px}
.social{left:304px;top:7px;display:flex;gap:6px}
.social i{width:18px;height:18px;border-radius:50%;background:#ddd;display:block}
.copy{right:74px;top:11px;font-size:7px;color:#ddd}
</style>
</head>
<body>

<div class="abs topbar">
  <span><svg width="9" height="9" viewBox="0 0 10 10"><path d="M2 0.5 L3.8 2.7 L2.9 3.9 Q3.8 5.9 6 7 L7.2 6.1 L9.5 7.9 L8.5 9.4 Q3.5 9.2 0.6 1.5 Z" fill="#ddd"/></svg>020 7946 0312</span>
  <span><svg width="10" height="8" viewBox="0 0 10 8"><rect x="0.5" y="0.5" width="9" height="7" fill="none" stroke="#ddd"/><path d="M0.5 0.5 L5 4.5 L9.5 0.5" fill="none" stroke="#ddd"/></svg>website@plumbwick.net</span>
</div>

<header class="abs header">
  <div class="abs brand"><i class="brand-mark"></i><span class="brand-name">plumbwick</span></div>
  <nav class="abs nav">
    <a class="active" href="#">Home</a><a href="#">About us</a><a href="#">What we do</a><a href="#">News blog</a><a href="#">Articles</a><a href="#">Clients</a><a href="#">Partners</a>
  </nav>
</header>

<section class="abs hero">
  <div class="abs hero-devices" role="img" aria-label="Desktop monitor and tablet showing a businessman touching a floating icon"></div>
  <h1 class="abs hero-title">Provides a high quality,<br>one-stop IT support<br>solution for your business</h1>
</section>
<div class="abs hero-arrows">
  <svg viewBox="0 0 20 20"><circle cx="10" cy="10" r="9" fill="#9aa3a3" stroke="#fff"/><path d="M11.5 6 L7.5 10 L11.5 14" stroke="#fff" stroke-width="1.5" fill="none"/></svg>
  <svg viewBox="0 0 20 20"><circle cx="10" cy="10" r="9" fill="#9aa3a3" stroke="#fff"/><path d="M8.5 6 L12.5 10 L8.5 14" stroke="#fff" stroke-width="1.5" fill="none"/></svg>
</div>

<h2 class="abs welcome-title">WELCOME</h2>
<div class="abs welcome-sub">plumbwick</div>
<div class="abs welcome-rule"></div>
<p class="abs welcome-text">Plumbwick was established with a specific aim: to consistently deliver an advanced and comprehensive IT service for ambitious growing companies across all industry sectors.</p>
<div class="abs divider"></div>

<div class="abs services">
  <div class="service"><div class="ico"><svg width="22" height="20" viewBox="0 0 22 20"><rect x="1" y="1" width="20" height="13" fill="none" stroke="#333" stroke-width="2"/><rect x="9" y="14" width="4" height="3" fill="#333"/><rect x="5" y="17" width="12" height="2" fill="#333"/></svg></div><div class="label">IT Support</div></div>
  <div class="service"><div class="ico"><svg width="24" height="18" viewBox="0 0 24 18"><circle cx="12" cy="4" r="3.2" fill="#333"/><circle cx="5" cy="7" r="2.8" fill="#333"/><circle cx="19" cy="7" r="2.8" fill="#333"/><path d="M6 18 Q6 9 12 9 Q18 9 18 18Z" fill="#333"/><path d="M0 17 Q0 11 5 11 Q7 11 7.5 12 L6 17Z M24 17 Q24 11 19 11 Q17 11 16.5 12 L18 17Z" fill="#333"/></svg></div><div class="label">Consultancy</div></div>
  <div class="service"><div class="ico"><svg width="20" height="22" viewBox="0 0 20 22"><circle cx="10" cy="3" r="2" fill="none" stroke="#333" stroke-width="1.5"/><path d="M9 5 L3 21 M11 5 L17 21 M4 14 Q10 17 16 14" fill="none" stroke="#333" stroke-width="1.6"/></svg></div><div class="label">CAD</div></div>
  <div class="service"><div class="ico"><svg width="22" height="20" viewBox="0 0 22 20"><rect x="1" y="1" width="9" height="11" fill="none" stroke="#333" stroke-width="1.4"/><path d="M3 4h5M3 7h5M3 10h5" stroke="#333"/><rect x="10" y="8" width="11" height="8" fill="none" stroke="#333" stroke-width="1.4"/><path d="M13 19h5M15.5 16v3" stroke="#333" stroke-width="1.4"/></svg></div><div class="label">Hosting</div></div>
  <div class="service"><div class="ico"><svg width="22" height="20" viewBox="0 0 22 20"><circle cx="8" cy="12" r="5" fill="none" stroke="#333" stroke-width="3" stroke-dasharray="2.5 1.5"/><circle cx="8" cy="12" r="1.5" fill="#333"/><circle cx="16" cy="5" r="3.2" fill="none" stroke="#333" stroke-width="2" stroke-dasharray="1.8 1.2"/></svg></div><div class="label">Development</div></div>
</div>

<section class="abs mission">
  <div class="abs mission-photo" role="img" aria-label="Smiling businessman in a dark suit and striped tie"></div>
  <h2>Our Mission</h2>
  <p class="lead">Plumbwick's mission is to be the premier IT services partner and provider of software, hardware and support solutions for progressive businesses.</p>
  <h3>To achieve this we shall:</h3>
  <ul>
    <li>Employ, encourage and empower quality members of staff who aspire to offer the highest level of service.</li>
    <li>Commit to always exceed the expectations of our customers.</li>
    <li>Commit to always exceed the expectations of our customers.</li>
  </ul>
</section>

<h2 class="abs testi-title">Client Testimonials</h2>
<div class="abs testi" style="left:84px;top:725px">
  <div class="avatar" role="img" aria-label="Portrait of male client"></div>
  <p><b>&ldquo;</b>Lorem ipsum donlor ameti coinsecte adsicn elit sed do eiusmod tempor incidwiunt utboret d magna aliqua. Ut enim ad minienia quis nostru exercitation ullamco laboriisi ut aliqup ex ea com co Nemo enim ipsam voluptatem quia voluptas.</p>
</div>
<div class="abs client" style="left:85px;top:817px">Mr. Client Name</div>
<div class="abs testi" style="left:346px;top:725px">
  <div class="avatar" role="img" aria-label="Portrait of female client"></div>
  <p><b>&ldquo;</b>Lorem ipsum donlor ameti coinsecte adsicn elit sed do eiusmod tempor incidwiunt utboret d magna aliqua. Ut enim ad minienia quis nostru exercitation ullamco laboriisi ut aliqup ex ea com co Nemo enim ipsam voluptatem quia voluptas.</p>
</div>
<div class="abs client" style="left:347px;top:817px">Mrs. Client Name</div>

<section class="abs team">
  <h2>Meet The Team</h2>
  <svg class="abs team-arrow" style="left:79px" viewBox="0 0 20 20"><circle cx="10" cy="10" r="9" fill="none" stroke="#333" stroke-width="1.2"/><path d="M11.5 6 L7.5 10 L11.5 14" stroke="#333" stroke-width="1.5" fill="none"/></svg>
  <svg class="abs team-arrow" style="left:579px" viewBox="0 0 20 20"><circle cx="10" cy="10" r="9" fill="none" stroke="#333" stroke-width="1.2"/><path d="M8.5 6 L12.5 10 L8.5 14" stroke="#333" stroke-width="1.5" fill="none"/></svg>
  <div class="team-row">
    <div class="member"><div class="photo" role="img" aria-label="Team member portrait"></div><span>Mrs. Member Name</span></div>
    <div class="member"><div class="photo" role="img" aria-label="Team member portrait"></div><span>Mr. Member Name</span></div>
    <div class="member"><div class="photo" role="img" aria-label="Team member portrait"></div><span>Mr. Member Name</span></div>
    <div class="member"><div class="photo" role="img" aria-label="Team member portrait"></div><span>Mrs. Member Name</span></div>
    <div class="member"><div class="photo" role="img" aria-label="Team member portrait"></div><span>Mrs. Member Name</span></div>
  </div>
</section>

<footer class="abs footer">
  <h4 style="left:74px">Quick Links</h4>
  <ul class="qlinks">
    <li>Home</li><li>Clients</li><li>About us</li><li>Partners</li><li>What we do</li><li>Contact</li><li>News blog</li><li>Support</li><li>Articles</li><li>Terms</li>
  </ul>
  <h4 style="left:201px">Latest News</h4>
  <div class="news" style="top:36px"><b>Lorem ipsum dolor sit</b>Sed diam nonmy nibh eumod tinci ut dolore magna aliquam erat volutpat.<br><i>12/JAN/2014</i></div>
  <div class="news" style="top:94px"><b>Lorem ipsum dolor sit</b>Sed diam nonmy nibh eumod tinci ut dolore magna aliquam erat volutpat.<br><i>12/JAN/2014</i></div>
  <h4 style="left:346px">Contact Information</h4>
  <div class="contact">
    <div class="row"><svg viewBox="0 0 10 10"><path d="M5 0.5 A3.3 3.3 0 0 1 8.3 3.8 Q8.3 6 5 9.5 Q1.7 6 1.7 3.8 A3.3 3.3 0 0 1 5 0.5Z" fill="#999"/><circle cx="5" cy="3.8" r="1.2" fill="#303030"/></svg><div>Plumbwick.net Ltd<br>Harrow House 48-52 Mill Lane<br>London N1 4QT<br>United Kingdom</div></div>
    <div class="row"><svg viewBox="0 0 10 10"><path d="M2 0.5 L3.8 2.7 L2.9 3.9 Q3.8 5.9 6 7 L7.2 6.1 L9.5 7.9 L8.5 9.4 Q3.5 9.2 0.6 1.5 Z" fill="#999"/></svg><b style="font-size:8px">020 7946 0312</b></div>
    <div class="row"><svg viewBox="0 0 10 8"><rect x="0.5" y="0.5" width="9" height="7" fill="none" stroke="#999"/><path d="M0.5 0.5 L5 4.5 L9.5 0.5" fill="none" stroke="#999"/></svg>website@plumbwick.net</div>
  </div>
  <h4 style="left:488px">Quick Contact</h4>
  <div class="qc-field" style="top:38px">Your Name</div>
  <div class="qc-field" style="top:62px">Your Email</div>
  <div class="qc-field" style="top:86px;height:34px">Your Message</div>
  <div class="abs qc-submit">SUBMIT</div>
</footer>

<div class="abs bottombar">
  <div class="abs sub-field">enter email for subcribe</div>
  <div class="abs sub-go">GO</div>
  <div class="abs social"><i></i><i></i><i></i><i></i></div>
  <div class="abs copy">© 2014 plumbwick. All right reserved.</div>
</div>

</body>
</html>
```